Medical VIP club - small design

Please read the specs in a design brief attached. Also we don't have logo in a Vector format and attaching the only version we have.

Club

```html
<!DOCTYPE html>
<html lang="en">
<head>
<meta charset="utf-8">
<title>Curalis – Services</title>
<link href="https://fonts.googleapis.com/css2?family=Arimo:wght@400;700&family=Tinos:wght@700&display=swap" rel="stylesheet">
<style>
:root{
  --header-top:#5f4f3c;
  --header-bottom:#7a6850;
  --frame:#5c4c38;
  --cream:#f3e8d6;
  --cream-dark:#d8c4a4;
  --tab-top:#b7a283;
  --tab-bottom:#7d6b53;
  --tab-green-top:#d3cf76;
  --tab-green-bottom:#9a9540;
  --tab-gold-top:#f4cf3a;
  --tab-gold-bottom:#bf960c;
  --olive-top:#8b8160;
  --olive-bottom:#675c3d;
  --table-head:#9b9545;
  --rule:#c9c9c9;
  --ink:#333333;
  --white:#ffffff;
  --logo:#f1e3c8;
  --logo-dark:#6b5438;
}
*{margin:0;padding:0;box-sizing:border-box}
html,body{width:1200px;height:874px;overflow:hidden}
body{font-family:"Arimo",Arial,sans-serif;background:var(--frame);position:relative}
.site-header{position:absolute;left:0;top:0;width:1200px;height:279px;
  background:linear-gradient(180deg,var(--header-top),var(--header-bottom))}
.brand{position:absolute;left:40px;top:72px;display:flex;align-items:center;gap:14px}
.brand-mark{width:46px;height:46px;border-radius:50%;background:var(--logo)}
.brand-name{font-size:60px;font-weight:700;color:var(--logo);letter-spacing:1px}
.phone{position:absolute;left:789px;top:53px;display:flex;align-items:center;gap:22px}
.phone-number{font-size:46px;font-weight:700;color:var(--white);
  text-shadow:0 2px 3px rgba(0,0,0,.6)}
.nav-band{position:absolute;left:0;top:240px;width:1200px;height:39px;
  background:linear-gradient(180deg,var(--cream),var(--cream-dark))}
.main-nav{position:absolute;left:24px;top:206px;display:flex;gap:4px}
.nav-tab{width:190px;height:73px;border-radius:12px 12px 0 0;
  background:linear-gradient(180deg,var(--tab-top),var(--tab-bottom));
  color:var(--white);font-size:20px;display:flex;align-items:center;justify-content:center;
  padding-top:2px;box-shadow:0 -1px 2px rgba(0,0,0,.35)}
.nav-tab.is-active{background:linear-gradient(180deg,var(--tab-green-top),var(--tab-green-bottom))}
.nav-tab.is-highlight{background:linear-gradient(180deg,var(--tab-gold-top),var(--tab-gold-bottom))}
.content-panel{position:absolute;left:24px;top:289px;width:1158px;height:485px;background:var(--white)}
.panel-title{position:absolute;left:5px;top:5px;width:1144px;height:54px;
  background:linear-gradient(180deg,var(--olive-top),var(--olive-bottom));
  color:var(--white);font-size:24px;padding:14px 0 0 16px;box-shadow:0 3px 4px rgba(0,0,0,.25)}
.package-table{position:absolute;left:24px;top:82px;width:1109px;border-collapse:collapse;font-size:14px;color:var(--ink)}
.package-table th{background:var(--table-head);color:var(--white);font-size:14px;font-weight:700;
  height:36px;border:1px solid var(--rule)}
.package-table td{height:35.5px;border:1px solid var(--rule);padding-left:20px}
.package-table td+td{padding-left:14px}
.package-table tfoot td{border:none;height:40px;padding:8px 0 0 0;text-align:center;
  font-family:"Tinos",serif;font-weight:700;font-size:14px}
.col-1{width:359px}.col-2{width:386px}
.site-footer{position:absolute;left:0;top:784px;width:1200px;height:90px;
  background:linear-gradient(180deg,var(--cream) 0%,var(--cream-dark) 45%,#9c8666 100%)}
.social{position:absolute;left:24px;top:28px;display:flex;gap:6px}
.social-link{width:37px;height:37px;border-radius:4px;background:var(--logo-dark)}
.copyright{position:absolute;left:0;width:1200px;top:45px;text-align:center;font-size:13px;color:#2d2418}
.footer-brand{position:absolute;right:22px;top:26px;display:flex;align-items:center;gap:8px}
.footer-brand .brand-mark{width:24px;height:24px;background:var(--logo-dark)}
.footer-brand .brand-name{font-size:32px;color:var(--logo-dark);letter-spacing:0}
</style>
</head>
<body>
<header class="site-header">
  <div class="brand"><span class="brand-mark"></span><span class="brand-name">Curalis</span></div>
  <div class="phone">
    <svg width="104" height="104" viewBox="0 0 104 104" aria-hidden="true">
      <defs><radialGradient id="phoneBall" cx="40%" cy="30%" r="70%">
        <stop offset="0" stop-color="#e3b25a"/><stop offset="1" stop-color="#6e4510"/></radialGradient></defs>
      <circle cx="52" cy="52" r="50" fill="#f0e4cc"/>
      <circle cx="52" cy="52" r="45" fill="url(#phoneBall)"/>
      <path d="M24 44c0-10 56-10 56 0v6h-14v-5c-6-3-22-3-28 0v5H24z" fill="#fff"/>
      <path d="M36 52h32l8 22H28z" fill="#fff"/>
      <circle cx="52" cy="63" r="6" fill="#9a6a25"/>
    </svg>
    <span class="phone-number">555-010-200</span>
  </div>
</header>
<div class="nav-band"></div>
<nav class="main-nav">
  <a class="nav-tab">About Us</a>
  <a class="nav-tab">VIP Club</a>
  <a class="nav-tab is-active">Services</a>
  <a class="nav-tab">Packages &amp; Prices</a>
  <a class="nav-tab is-highlight">Registration</a>
  <a class="nav-tab">Contacts</a>
</nav>
<main class="content-panel">
  <h1 class="panel-title" style="font-weight:400">Services</h1>
  <table class="package-table">
    <thead><tr><th class="col-1">Package 1</th><th class="col-2">Package 2</th><th>Package 3</th></tr></thead>
    <tbody>
      <tr><td>-Lorem ipsum</td><td>-Lorem ipsum</td><td>-Lorem ipsum</td></tr>
      <tr><td>-Lorem ipsum</td><td>-Lorem ipsum</td><td>-Lorem ipsum</td></tr>
      <tr><td>-Lorem ipsum</td><td>-Lorem ipsum</td><td>-Lorem ipsum</td></tr>
      <tr><td>-Lorem ipsum</td><td>-Lorem ipsum</td><td>-Lorem ipsum</td></tr>
      <tr><td>-Lorem ipsum</td><td>-Lorem ipsum</td><td>-Lorem ipsum</td></tr>
      <tr><td>-Lorem ipsum</td><td>-Lorem ipsum</td><td>-Lorem ipsum</td></tr>
      <tr><td>-Lorem ipsum</td><td>-Lorem ipsum</td><td>-Lorem ipsum</td></tr>
      <tr><td>-Lorem ipsum</td><td>-Lorem ipsum</td><td>-Lorem ipsum</td></tr>
      <tr><td>-Lorem ipsum</td><td>-Lorem ipsum</td><td>-Lorem ipsum</td></tr>
    </tbody>
    <tfoot><tr><td>$000</td><td>$000</td><td>$000</td></tr></tfoot>
  </table>
</main>
<footer class="site-footer">
  <div class="social">
    <span class="social-link" aria-label="Social link"></span>
    <span class="social-link" aria-label="Social link"></span>
    <span class="social-link" aria-label="Feed link"></span>
  </div>
  <p class="copyright">Copyright ©2010 Curalis. All Rights Reserved</p>
  <div class="footer-brand"><span class="brand-mark"></span><span class="brand-name">Curalis</span></div>
</footer>
</body>
</html>
```